BRISKLY sparkling water needs new artwork! Based in Southern California

"Briskly" is a new sparkling water company based in Southern California that offers refreshing flavors (lime, cherry, & mango) with B vitamins and antioxidants.

We would like to see packaging designs for standard 12oz cans for each of the three flavors.
Our initial preference is to have individual artwork for each flavor.

Attached are examples of competitors' designs.
Updates

We are extending the deadline for the Thanksgiving Holiday. Thank you all for your contributions.

```html
<!DOCTYPE html>
<html lang="en">
<head>
<meta charset="utf-8">
<title>Briskly Sparkling Water – Lime Can Label</title>
<link rel="stylesheet" href="https://fonts.googleapis.com/css2?family=Oswald:wght@600&family=Courgette&family=Montserrat:wght@500;600&family=Fredoka:wght@700&display=swap">
<style>
  :root {
    --backdrop: #a39e0e;
    --label-white: #f4f4f2;
    --citrus: #d9d21f;
    --brand-yellow: #d6ce13;
    --fruit-light: #f6e14a;
    --fruit-mid: #e9c11c;
    --ink: #141414;
  }
  * { margin: 0; padding: 0; box-sizing: border-box; }
  html, body { width: 1200px; height: 1133px; overflow: hidden; }
  body { background: var(--backdrop); position: relative; font-family: "Montserrat", sans-serif; color: var(--ink); }

  .can-label {
    position: absolute; left: 290px; top: 60px;
    width: 620px; height: 1013px;
    background: var(--label-white);
    border-radius: 18px;
    overflow: hidden;
  }
  .label-bands { position: absolute; inset: 0; }

  .brand-name {
    position: absolute; left: 0; right: 0; top: 95px;
    text-align: center;
    font-family: "Oswald", sans-serif; font-weight: 600;
    font-size: 150px; line-height: 1; letter-spacing: 1px;
    color: var(--brand-yellow);
    transform: scaleY(1.08);
  }
  .product-type {
    position: absolute; left: 0; right: 0; top: 262px;
    text-align: center;
    font-family: "Courgette", cursive;
    font-size: 58px; line-height: 1;
  }
  .tagline {
    position: absolute; left: 0; right: 0; top: 352px;
    text-align: center;
    font-size: 15px; font-weight: 500; letter-spacing: 1.5px;
  }
  .tagline span { background: var(--label-white); padding: 0 12px; }

  .fruit-illustration {
    position: absolute; left: 115px; top: 400px;
    width: 390px; height: 330px;
    border-radius: 40px;
    background: radial-gradient(ellipse at 50% 45%, var(--fruit-light) 0%, var(--fruit-mid) 45%, #f7f4d8 80%, #fbfaef 100%);
  }

  .flavor-name {
    position: absolute; left: 0; right: 0; top: 745px;
    text-align: center;
    font-family: "Fredoka", sans-serif; font-weight: 700;
    font-size: 76px; line-height: 1;
    color: var(--label-white);
    -webkit-text-stroke: 4px var(--ink);
    paint-order: stroke fill;
  }
  .benefits {
    position: absolute; left: 0; right: 0; top: 840px;
    text-align: center; font-size: 18px; font-weight: 600; letter-spacing: 0.5px;
  }
  .maker {
    position: absolute; left: 0; right: 0; top: 870px;
    text-align: center;
    font-family: "Oswald", sans-serif; font-weight: 600; font-size: 17px;
  }
  .origin {
    position: absolute; left: 0; right: 0; top: 898px;
    text-align: center; font-size: 14px; font-weight: 500;
  }
  .volume {
    position: absolute; left: 0; right: 0; top: 924px;
    text-align: center;
    font-family: "Oswald", sans-serif; font-weight: 600; font-size: 38px;
  }
</style>
</head>
<body>
  <main class="can-label">
    <svg class="label-bands" viewBox="0 0 620 1013" aria-hidden="true">
      <path d="M0 700 C 140 600, 420 560, 620 590 L620 1013 L0 1013 Z" fill="var(--citrus)"/>
      <path d="M0 630 C 150 520, 420 480, 620 510" fill="none" stroke="var(--citrus)" stroke-width="22"/>
      <line x1="30" y1="362" x2="590" y2="362" stroke="var(--ink)" stroke-width="1.5"/>
    </svg>

    <h1 class="brand-name">BRISKLY</h1>
    <p class="product-type">Sparkling Water</p>
    <p class="tagline"><span>REFRESHING FLAVORS</span></p>

    <div class="fruit-illustration" role="img" aria-label="Illustration of whole and sliced lemons with green leaves inside a wavy outlined frame with burst lines"></div>

    <p class="flavor-name">lime</p>
    <p class="benefits">B VITAMINS AND ANTIOXIDANTS</p>
    <p class="maker">CREATED BY BRISKLY</p>
    <p class="origin">Based in Southern California</p>
    <p class="volume">12oz</p>
  </main>
</body>
</html>
```